Corvane Card

The logo is the Spanish flag colors I want a vibrant eye catching design with the yellow / red colors over either Navy or white background or black even ,
Would like a 2D feel to the logo with another lighter color logo under it look ,

Contact Information for Business Card

Corvane Flooring
Teodor Vashkin
Main Number
Cell Number
Fax Number

Website on the side of the card somewhere

Font styles to use
Sans Serif

Colors
ec1f27
ffc214

Requirements
Must have
• 2 logos feel one is bolder and the other one underneath very light

```html
<!DOCTYPE html>
<html lang="en">
<head>
<meta charset="utf-8">
<title>Corvane Flooring — Business Card</title>
<link href="https://fonts.googleapis.com/css2?family=Jost:wght@500;600;700&family=Arimo:wght@400&display=swap" rel="stylesheet">
<style>
  :root {
    --red: #ec1f27;
    --yellow: #ffc214;
    --card: #0b0b0b;
    --backdrop: #2a2a2a;
    --text: #ffffff;
    --divider: #2c2c2c;
  }
  html, body {
    margin: 0;
    width: 1200px;
    height: 900px;
    overflow: hidden;
    background: radial-gradient(ellipse at 40% 20%, #3a3a3a 0%, var(--backdrop) 55%, #161616 100%);
    font-family: "Jost", sans-serif;
  }
  .card {
    position: absolute;
    width: 620px;
    height: 354px;
    background: var(--card);
    box-shadow: 0 18px 40px rgba(0,0,0,.55);
    box-sizing: border-box;
  }
  .card--front { left: 60px; top: 80px; }
  .card--back  { left: 520px; top: 466px; display: flex; align-items: center; justify-content: center; }

  .brand { display: flex; flex-direction: column; align-items: flex-start; color: var(--red); font-weight: 700; }
  .brand__mark { width: 46px; height: 46px; background: var(--red); margin-bottom: 14px; }
  .brand__name { font-size: 34px; letter-spacing: 1px; line-height: 1; }
  .brand__sub { font-size: 17px; letter-spacing: 12px; margin-top: 8px; }

  .card--front .brand { position: absolute; left: 40px; top: 118px; }
  .card--front .brand__name { font-size: 28px; }
  .card--front .brand__sub { font-size: 14px; letter-spacing: 10px; }

  .divider { position: absolute; left: 262px; top: 40px; bottom: 40px; width: 1px; background: var(--divider); }

  .contact { position: absolute; left: 300px; top: 88px; }
  .contact__name { font-size: 25px; font-weight: 600; letter-spacing: .5px; margin: 0 0 18px; }
  .contact__first { color: var(--red); }
  .contact__last { color: var(--yellow); }
  .contact__list { list-style: none; margin: 0; padding: 0; font-family: "Arimo", sans-serif; color: var(--text); font-size: 15px; }
  .contact__list li { display: flex; align-items: center; gap: 10px; height: 24px; }
  .contact__list svg { width: 14px; height: 14px; fill: var(--red); flex: none; }
  .accent { color: var(--red); }
</style>
</head>
<body>

<section class="card card--front" aria-label="Business card front">
  <div class="brand">
    <span class="brand__mark"></span>
    <span class="brand__name">CORVANE</span>
    <span class="brand__sub">FLOORING</span>
  </div>

  <div class="divider"></div>

  <div class="contact">
    <h1 class="contact__name"><span class="contact__first">TEODOR</span> <span class="contact__last">VASHKIN</span></h1>
    <ul class="contact__list">
      <li><svg viewBox="0 0 16 16" aria-hidden="true"><path d="M1 6c0-2 3-3 7-3s7 1 7 3v1h-4V5.5H5V7H1zM4 8h8l2 6H2z"/></svg>312 555 0147</li>
      <li><svg viewBox="0 0 16 16" aria-hidden="true"><path d="M4 1h8v14H4zM5.5 2.5v9h5v-9z"/></svg>312 555 0192</li>
      <li><svg viewBox="0 0 16 16" aria-hidden="true"><path d="M4 1h8v4H4zM1 6h14v7h-3v2H4v-2H1zM5 10v4h6v-4z"/></svg>312 555 0175</li>
      <li><svg viewBox="0 0 16 16" aria-hidden="true"><path d="M1 3h14v10H1zM2.5 4.5 8 9l5.5-4.5z"/></svg>hello@corvaneflooring.com</li>
      <li><svg viewBox="0 0 16 16" aria-hidden="true"><circle cx="8" cy="8" r="7"/></svg>www.<span class="accent">corvaneflooring</span>.com</li>
    </ul>
  </div>
</section>

<section class="card card--back" aria-label="Business card back">
  <div class="brand">
    <span class="brand__mark"></span>
    <span class="brand__name">CORVANE</span>
    <span class="brand__sub">FLOORING</span>
  </div>
</section>

</body>
</html>
```